Fitness Equipment & Service

I want to make the card eye catching and fun. We are called Corvane Motion Limited and we are based in Wales. We sell, install and service all types of fitness equipment from Skipping ropes, right through the Dumbbells, Kettle bells and Barbells through to state of the art Treadmills, Running Machines and Strength Equipment. We also design and install changing room furniture and lockers.

TYPOGRAPHY
We would like to use Futrura. Futura has an appearance of efficiency and forwardness. The typeface is derived
from simple geometric forms (near-perfect circles, triangles and squares) and is based on strokes of
near-even weight, which are low in contrast. This is most visible in the almost perfectly round stroke of
the o, which is nonetheless slightly ovoid.
The lowercase has tall ascenders, which rise above the cap line. The uppercase
characters present proportions similar to those of classical Roman capitals.

TYPOGRAPHIC CONSIDERATIONS
No Strike though
No Horizontal Scaling
No Drop Shadows
No Effects
Never use less than 120% Leading

OUR CORPORATE COLOURS
BRAND GUIDELINES
We were thinking that our primary colour palette consists of the Acid Green (Pantone 382) and Process Black.

We work closely with tquarly Ltd and would like to include their name on the card somewhere. I have attached images of the other brands that we work with as an idea or the small icons I have included that illustrate what we do?. I have very kindly been given permission to use any of the images off the files that I have included below, so I hope these help. I will include these below. I would be open to suggestions if it made the card more striking Can you do it?
Updates

Hi All, Just wanted to add a few thoughts but you are the guys with the creative visions (thats why are here) We are based in Wales, UK and we would be open to lots of different ideas on a theme but must be eye catching, Bold and FUN. If you can or think that the Welsh or any dragon could be put in there then go for it (its not a must have) We have also added some ideas for colour but again its over to you!! GO FOR IT ! Thanks and look forward to your visions! Owen

Hi All, Just thought I would sen through the contact details that need to be on the card. (if you want to play around with icons instead of the wording twitter, Facebook, go for it): Corvane Motion Limited Owen Pritchard Managing Director Mob: +44 (0)7582 913 406 e-mail: sales@corvanemotion.co.uk Web: Corvanemotion.co.uk twitter: @motionLetterbin Facebook: Corvane Motion Limited

```html
<!DOCTYPE html>
<html lang="en">
<head>
<meta charset="utf-8">
<title>Corvane Motion Limited – Business Card</title>
<link rel="stylesheet" href="https://fonts.googleapis.com/css2?family=Jost:wght@400;500;700&family=Arimo:wght@400;700&display=swap">
<style>
  :root {
    --page-bg: #e9e7e3;
    --card-white: #ffffff;
    --card-grey: #d9d9d9;
    --navy: #16245a;
    --navy-deep: #0d1a4a;
    --blue-band-start: #1a2f7a;
    --blue-band-end: #2a4a9e;
    --gold-start: #9e7f3c;
    --gold-end: #d8bd7a;
    --text-grey: #555a63;
    --icon-navy: #1f2d66;
  }
  * { box-sizing: border-box; margin: 0; padding: 0; }
  html, body {
    width: 1200px; height: 950px; overflow: hidden;
    background: var(--page-bg);
  }
  .canvas {
    width: 1200px; height: 950px;
    display: flex; flex-direction: column; align-items: center; justify-content: center;
    gap: 22px;
  }
  .card {
    position: relative;
    width: 780px; height: 446px;
    border-radius: 4px;
    overflow: hidden;
    box-shadow: 0 2px 6px rgba(0,0,0,0.15);
  }

  /* Back of card */
  .card-back {
    background: linear-gradient(160deg, var(--card-white) 0%, #f1f1f1 50%, var(--card-grey) 100%);
    display: flex; flex-direction: column; align-items: center; justify-content: center;
    gap: 22px;
  }
  .back-mark {
    width: 150px; height: 150px; border-radius: 50%;
    background: radial-gradient(circle at 40% 35%, var(--blue-band-end), var(--navy-deep));
  }
  .back-name {
    font-family: "Jost", sans-serif;
    font-weight: 500;
    font-size: 24px;
    letter-spacing: 2px;
    text-transform: uppercase;
    color: var(--navy);
    line-height: 1.2;
  }

  /* Front of card */
  .card-front { background: var(--card-white); }
  .brand {
    position: absolute; left: 52px; top: 46px;
    display: flex; align-items: center; gap: 16px;
  }
  .brand-dot {
    width: 54px; height: 54px; border-radius: 50%;
    background: var(--navy);
  }
  .brand-name {
    font-family: "Jost", sans-serif;
    font-weight: 700;
    font-size: 34px;
    line-height: 1.2;
    letter-spacing: 1px;
    text-transform: uppercase;
    color: var(--navy);
  }
  .band-blue {
    position: absolute; left: 0; top: 136px;
    width: 560px; height: 74px;
    background: linear-gradient(90deg, var(--blue-band-start), var(--blue-band-end));
  }
  .band-gold {
    position: absolute; left: 560px; top: 168px;
    width: 220px; height: 56px;
    background: linear-gradient(90deg, var(--gold-start), var(--gold-end));
  }
  .band-emblem {
    position: absolute; left: 520px; top: 132px;
    width: 96px; height: 96px; border-radius: 50%;
    background: radial-gradient(circle at 40% 35%, var(--blue-band-end), var(--navy-deep));
    border: 3px solid #e6e6e6;
  }
  .person {
    position: absolute; left: 52px; top: 146px;
    font-family: "Arimo", sans-serif;
    color: var(--card-white);
    line-height: 1.2;
  }
  .person-name { font-weight: 700; font-size: 26px; }
  .person-role { font-weight: 400; font-size: 19px; margin-top: 2px; }

  .contact {
    position: absolute; left: 52px; top: 262px;
    list-style: none;
    font-family: "Arimo", sans-serif;
    font-size: 19px;
    line-height: 1.3;
    color: var(--text-grey);
  }
  .contact li { display: flex; align-items: center; gap: 10px; }
  .contact svg { width: 18px; height: 18px; flex: none; }

  .address {
    position: absolute; right: 48px; bottom: 50px;
    font-family: "Arimo", sans-serif;
    font-size: 19px;
    line-height: 1.3;
    color: var(--text-grey);
    text-align: left;
  }
</style>
</head>
<body>
<main class="canvas">

  <section class="card card-back" aria-label="Card back">
    <div class="back-mark"></div>
    <p class="back-name">Corvane Motion Limited</p>
  </section>

  <section class="card card-front" aria-label="Card front">
    <div class="brand">
      <div class="brand-dot"></div>
      <p class="brand-name">Corvane Motion Limited</p>
    </div>

    <div class="band-blue"></div>
    <div class="band-gold"></div>
    <div class="band-emblem"></div>

    <div class="person">
      <p class="person-name">Owen Pritchard</p>
      <p class="person-role">Managing Director</p>
    </div>

    <ul class="contact">
      <li>
        <svg viewBox="0 0 18 18" aria-hidden="true"><rect x="4" y="1" width="10" height="16" rx="2" fill="none" stroke="var(--icon-navy)" stroke-width="2"/><rect x="7" y="13" width="4" height="1.6" fill="var(--icon-navy)"/></svg>
        +44 (0)7582 913 406
      </li>
      <li>
        <svg viewBox="0 0 18 18" aria-hidden="true"><rect x="1" y="4" width="16" height="11" fill="var(--icon-navy)"/><path d="M1 4 L9 10 L17 4" fill="none" stroke="#fff" stroke-width="1.4"/></svg>
        sales@corvanemotion.co.uk
      </li>
      <li>
        <svg viewBox="0 0 18 18" aria-hidden="true"><circle cx="9" cy="9" r="8" fill="var(--icon-navy)"/><path d="M1 9 H17 M9 1 C5 5 5 13 9 17 M9 1 C13 5 13 13 9 17" fill="none" stroke="#fff" stroke-width="1"/></svg>
        Corvanemotion.co.uk
      </li>
    </ul>

    <address class="address" style="font-style: normal;">
      4217 Harrowgate Lane<br>
      Birchfield, NY 11420
    </address>
  </section>

</main>
</body>
</html>
```